Business card for a new cabinet shop company named Veloran Cabinets for high end cabinets

Design a business card, thinking dark rich green with colours to speak of high end luxury ie; cream, gold, black possibly

Mitchell Tarrowby
Director Craftsman
Email: info@veloranjoinery-example.com.au
Instagram : @veloran.cabinets

```html
<!DOCTYPE html>
<html lang="en">
<head>
<meta charset="utf-8">
<title>Veloran Cabinets – Business Card</title>
<link href="https://fonts.googleapis.com/css2?family=Montserrat:wght@300;400;500;700&display=swap" rel="stylesheet">
<style>
  :root {
    --stage-dark: #111112;
    --stage-mid: #2b2b2d;
    --card-green: #5e9a45;
    --card-green-deep: #4c8436;
    --card-green-light: #77b05a;
    --card-black: #1b1b1c;
    --card-black-edge: #262627;
    --gold: #c9a66b;
    --white: #f4f2ee;
    --muted: #d9d6d0;
  }
  * { box-sizing: border-box; margin: 0; padding: 0; }
  html, body { width: 1200px; height: 875px; overflow: hidden; }
  body {
    background: radial-gradient(ellipse at 60% 40%, var(--stage-mid), var(--stage-dark) 75%);
    font-family: "Montserrat", sans-serif;
    position: relative;
  }
  .card {
    position: absolute;
    width: 540px;
    height: 310px;
    border-radius: 16px;
    overflow: hidden;
    box-shadow: 0 24px 50px rgba(0,0,0,0.55);
  }

  /* Front */
  .card--front { left: 50px; top: 150px; }
  .front-pattern {
    position: absolute; inset: 0;
    background: linear-gradient(125deg, var(--card-green-light) 0%, var(--card-green) 45%, var(--card-green-deep) 100%);
  }
  .front-brand {
    position: absolute;
    right: 44px;
    top: 50%;
    transform: translateY(-50%);
    display: flex;
    align-items: center;
    gap: 12px;
    padding: 14px 18px;
    background: var(--card-green);
    border-radius: 6px;
  }
  .brand-mark {
    width: 14px; height: 14px;
    border: 2px solid var(--gold);
  }
  .front-brand .brand-name {
    color: var(--gold);
    font-size: 24px;
    font-weight: 500;
    letter-spacing: 0.5px;
  }

  /* Back */
  .card--back {
    left: 610px; top: 420px;
    background: linear-gradient(135deg, var(--card-black-edge), var(--card-black));
  }
  .back-brand {
    position: absolute;
    left: 48px; top: 62px;
    display: flex; align-items: center; gap: 16px;
  }
  .back-brand .brand-mark { width: 22px; height: 22px; border-width: 3px; }
  .back-brand .brand-name {
    color: var(--gold);
    font-size: 38px;
    font-weight: 500;
    letter-spacing: 0.5px;
  }
  .holder {
    position: absolute;
    left: 48px; bottom: 52px;
  }
  .holder-name {
    font-size: 20px;
    color: var(--white);
    white-space: nowrap;
  }
  .holder-name .first { font-weight: 700; }
  .holder-name .last { font-weight: 300; color: var(--gold); }
  .holder-role {
    margin-top: 3px;
    font-size: 11px;
    font-weight: 400;
    color: var(--muted);
    letter-spacing: 0.3px;
  }
  .divider {
    position: absolute;
    left: 262px; bottom: 40px;
    width: 1px; height: 78px;
    background: var(--gold);
  }
  .contact {
    position: absolute;
    left: 278px; bottom: 42px;
    list-style: none;
    font-size: 10.5px;
    color: var(--white);
    display: flex; flex-direction: column; gap: 9px;
  }
  .contact li { display: flex; align-items: center; gap: 7px; white-space: nowrap; }
  .contact svg { flex: none; }
  .dot { width: 10px; height: 10px; border-radius: 50%; background: var(--gold); flex: none; }
</style>
</head>
<body>

  <section class="card card--front">
    <div class="front-pattern" role="img" aria-label="Repeating embossed monogram pattern in tonal green with gold foil sheen"></div>
    <div class="front-brand">
      <span class="brand-mark"></span>
      <span class="brand-name">Veloran Cabinets</span>
    </div>
  </section>

  <section class="card card--back">
    <div class="back-brand">
      <span class="brand-mark"></span>
      <span class="brand-name">Veloran Cabinets</span>
    </div>

    <div class="holder">
      <p class="holder-name"><span class="first">Mitchell</span> <span class="last">Tarrowby</span></p>
      <p class="holder-role">Director Craftsman</p>
    </div>

    <span class="divider"></span>

    <ul class="contact">
      <li>
        <svg width="11" height="8" viewBox="0 0 11 8" aria-hidden="true">
          <rect x="0.5" y="0.5" width="10" height="7" fill="none" stroke="#c9a66b"/>
          <path d="M0.5 0.5 L5.5 4.5 L10.5 0.5" fill="none" stroke="#c9a66b"/>
        </svg>
        info@veloranjoinery-example.com.au
      </li>
      <li><span class="dot"></span>@veloran.cabinets</li>
      <li>Western Australia</li>
    </ul>
  </section>

</body>
</html>
```